Dancing Emoji Lady but make it silhouette

We need a main image for the front of a hard wine seltzer. The best emoji that would describe this brand is the dancing lady in red dress emoji. We want to re-create the essence of this emoji in a silhouette (like an outline) so it's our own design, but it captures the fun and flirtatiousness of that emoji. We have three flavors - peach (peach color), fruit punch (red/purple color), and citrus (orange color) - so the only color should be the outline of her swooshing dress.

I'm attaching an image of the emoji I wish to emulate, and then some examples of what I mean by "silhouette" - I know the attached examples are not of a woman dancing, but it's the line/style that I want to emulate here to make a silhouette of the dancer emoji.

```html
<!DOCTYPE html>
<html lang="en">
<head>
<meta charset="utf-8">
<title>Calla Peach Bellini – Can Label</title>
<link href="https://fonts.googleapis.com/css2?family=Fraunces:opsz,wght@9..144,600;9..144,700&family=Oswald:wght@300;400;500&display=swap" rel="stylesheet">
<style>
  :root {
    --backdrop: #e8e8e8;
    --label: #ffffff;
    --band: #fde6de;
    --peach: #f4a593;
    --peach-soft: #fbe0d6;
    --navy: #323a5a;
    --dress-red: #a8141c;
    --line-wine: #4a1a1e;
  }
  html, body {
    margin: 0;
    padding: 0;
    width: 1200px;
    height: 739px;
    overflow: hidden;
    background: var(--backdrop);
  }
  .canvas {
    position: relative;
    width: 1200px;
    height: 739px;
  }
  .label {
    position: absolute;
    left: 450px;
    top: 127px;
    width: 301px;
    height: 485px;
    background: var(--label);
  }
  .claims-band {
    position: absolute;
    left: 0;
    top: 30px;
    width: 100%;
    height: 15px;
    background: var(--band);
    display: flex;
    align-items: center;
    justify-content: center;
    gap: 9px;
    font-family: "Oswald", sans-serif;
    font-weight: 400;
    font-size: 8px;
    letter-spacing: 0.4px;
    color: var(--peach);
  }
  .claims-band .dot {
    width: 2px;
    height: 2px;
    border-radius: 50%;
    background: #ffffff;
  }
  .brand-mark {
    position: absolute;
    left: 143px;
    top: 57px;
    width: 16px;
    height: 16px;
    border-radius: 50%;
    background: var(--navy);
  }
  .brand-name {
    position: absolute;
    left: 0;
    top: 74px;
    width: 100%;
    text-align: center;
    font-family: "Fraunces", serif;
    font-weight: 700;
    font-size: 52px;
    line-height: 1;
    color: var(--navy);
    letter-spacing: -1px;
  }
  .tagline-lettering {
    position: absolute;
    left: 118px;
    top: 137px;
    width: 66px;
    height: 12px;
    border-radius: 6px;
    background: var(--peach-soft);
  }
  .dancer-illustration {
    position: absolute;
    left: 74px;
    top: 159px;
    width: 135px;
    height: 182px;
    border-radius: 4px;
    background: linear-gradient(180deg, #fbeeee 0%, #f3d6d6 45%, #fbf1f1 100%);
  }
  .flavor {
    position: absolute;
    left: 0;
    top: 344px;
    width: 100%;
    text-align: center;
    font-family: "Oswald", sans-serif;
    font-weight: 300;
    font-size: 27px;
    line-height: 1;
    color: var(--peach);
    letter-spacing: 0.3px;
  }
  .product-type {
    position: absolute;
    left: 0;
    top: 376px;
    width: 100%;
    text-align: center;
    font-family: "Fraunces", serif;
    font-weight: 600;
    font-size: 12.5px;
    line-height: 1;
    color: var(--navy);
  }
  .badges {
    position: absolute;
    left: 0;
    top: 400px;
    width: 100%;
    display: flex;
    justify-content: center;
    gap: 10px;
  }
  .badge {
    width: 27px;
    height: 27px;
    border-radius: 50%;
    background: var(--peach-soft);
  }
  .specs {
    position: absolute;
    left: 0;
    top: 436px;
    width: 100%;
    text-align: center;
    font-family: "Oswald", sans-serif;
    font-weight: 400;
    font-size: 8px;
    color: var(--navy);
    letter-spacing: 0.2px;
  }
  .specs .divider { padding: 0 3px; }
</style>
</head>
<body>
<div class="canvas">
  <section class="label">
    <div class="claims-band">
      <span class="dot"></span><span>4G SUGAR</span>
      <span class="dot"></span><span>GLUTEN-FREE</span>
      <span class="dot"></span><span>120 CALORIES</span>
      <span class="dot"></span><span>WOMEN-OWNED</span>
      <span class="dot"></span>
    </div>
    <div class="brand-mark"></div>
    <div class="brand-name">calla</div>
    <div class="tagline-lettering" role="img" aria-label="Hand-lettered brand tagline in peach script"></div>
    <div class="dancer-illustration" role="img" aria-label="Line illustration of a woman dancing in a swirling red dress, holding a glass of wine"></div>
    <div class="flavor">PEACH BELLINI</div>
    <div class="product-type">Hard Wine Seltzer</div>
    <div class="badges">
      <div class="badge"></div>
      <div class="badge"></div>
      <div class="badge"></div>
    </div>
    <div class="specs">6% ABV<span class="divider">|</span>250 mL</div>
  </section>
</div>
</body>
</html>
```